Linden Medical - Flyer

We are a full service pharmacy that specializes in diabetic testing and medications. We research the patient's insurance to maximize their insurance benefit and then deliver the medications monthly directly to the patient's doorstep, for free! We save the patient, time and money every month.
We would love a flyer that we can distribute to Doctor's offices and patients that sum up our pharmacy. Emphasis on saving money, time, and getting the best quality supplies by maximizing their insurance. We want it to be eye catching, clean, and professional.
You can use our logo or feel free to make your own design.
diabetic patients wanting to save money
Insurance

```html
<!DOCTYPE html>
<html lang="en">
<head>
<meta charset="utf-8">
<title>Linden Medical – Flyers</title>
<link href="https://fonts.googleapis.com/css2?family=Oswald:wght@400;600;700&family=Open+Sans:wght@400;600;700&display=swap" rel="stylesheet">
<style>
  :root{
    --orange:#f28a1e;
    --blue:#2f7fc4;
    --blue-dark:#1f5f9e;
    --blue-light:#5aa4de;
    --green:#7dbb2f;
    --green-soft:#e4edd4;
    --ink:#3d3d3d;
    --grey:#6b6b6b;
    --paper:#ffffff;
    --stage:#ecebe8;
  }
  *{margin:0;padding:0;box-sizing:border-box}
  html,body{width:1200px;height:1000px;overflow:hidden;background:var(--stage)}
  body{position:relative;font-family:"Open Sans",sans-serif;color:var(--ink)}
  .flyer{position:absolute;top:100px;width:520px;height:800px;background:var(--paper);overflow:hidden;box-shadow:0 6px 20px rgba(0,0,0,.18)}
  .flyer--savings{left:50px}
  .flyer--pharmacy{left:630px}
  .photo{position:absolute}
  .brand{position:absolute;display:flex;align-items:center;gap:8px}
  .brand__mark{width:26px;height:26px;background:var(--green)}
  .brand__name{font-family:"Open Sans",sans-serif;font-weight:600;font-size:20px;letter-spacing:1px;color:var(--grey);text-transform:uppercase}
  .bands{position:absolute;left:0;width:520px}
  .headline{position:absolute;font-family:"Oswald",sans-serif;text-transform:uppercase}
  /* savings flyer */
  .savings__photo{left:0;top:0;width:520px;height:310px;background:linear-gradient(120deg,#d9cbb8 0%,#efe7dc 45%,#e9ecef 75%,#f5f6f7 100%)}
  .savings__brand{top:100px;right:34px}
  .savings__headline{top:148px;right:34px;text-align:right}
  .savings__headline .big{display:block;font-size:50px;font-weight:700;color:var(--orange);line-height:1}
  .savings__headline .sub{display:block;font-size:19px;font-weight:600;color:var(--ink);line-height:1.15;margin-top:4px}
  .features{position:absolute;top:352px;left:28px;right:30px;list-style:none}
  .feature{display:flex;gap:16px;margin-bottom:14px}
  .feature__icon{flex:0 0 40px;height:40px}
  .feature__title{font-family:"Oswald",sans-serif;font-weight:600;font-size:15px;line-height:1.4;color:var(--orange);text-transform:uppercase}
  .feature__title small{font-size:12px;text-transform:none;font-weight:400}
  .feature__text{font-size:10.5px;line-height:1.45;color:var(--grey)}
  .savings__cta{position:absolute;left:28px;right:20px;top:650px;font-size:12.5px;line-height:1.4;color:var(--ink)}
  .footer{position:absolute;left:0;bottom:0;width:520px;height:96px;background:linear-gradient(180deg,var(--blue-light),var(--blue-dark));color:#fff;font-size:13px;font-weight:600}
  .footer__item{position:absolute;display:flex;align-items:center;gap:8px;white-space:nowrap}
  .footer__item svg{width:16px;height:16px}
  .footer__item--phone{left:28px;top:14px}
  .footer__item--web{left:150px;top:40px}
  .footer__item--mail{left:300px;top:66px}
  /* pharmacy flyer */
  .pharmacy__photo{right:0;top:0;width:260px;height:320px;background:linear-gradient(160deg,#f4f1ec,#e6dccf 55%,#f1efeb)}
  .pharmacy__brand{top:40px;left:190px}
  .question{position:absolute;top:90px;left:36px;width:290px;padding:10px 14px;background:var(--green-soft)}
  .question p{font-family:"Oswald",sans-serif;text-transform:uppercase;line-height:1.05}
  .question .q1{font-size:20px;font-weight:600;color:var(--ink)}
  .question .q2{font-size:20px;font-weight:600;color:var(--orange)}
  .question .q3{font-size:34px;font-weight:700;color:var(--ink)}
  .badge{position:absolute;z-index:2;top:220px;right:30px;width:130px;height:130px}
  .badge svg{display:block}
  .badge__text{position:absolute;inset:0;display:flex;flex-direction:column;align-items:center;justify-content:center;color:#fff;text-align:center;font-family:"Oswald",sans-serif;line-height:1.05}
  .badge__text b{font-size:26px;line-height:1}
  .badge__text span{font-size:10.5px;margin-top:2px}
  .intro{position:absolute;top:366px;left:30px;width:260px;font-family:"Oswald",sans-serif;font-size:17px;font-weight:600;color:var(--orange);line-height:1.15}
  .col{position:absolute;font-size:10.5px;line-height:1.45;color:var(--grey)}
  .col p{margin-bottom:8px}
  .col--left{top:440px;left:30px;width:220px}
  .col--right{top:380px;left:300px;width:200px}
  .pharmacy__shelf{left:30px;top:530px;width:220px;height:120px;background:linear-gradient(135deg,#e9e4de,#c9b9a6 60%,#d8d2ca)}
  .pharmacy__test{left:270px;top:560px;width:220px;height:110px;background:linear-gradient(135deg,#f3f3f2,#dfd6cd 60%,#eeeeec)}
</style>
</head>
<body>

<section class="flyer flyer--savings">
  <div class="photo savings__photo" role="img" aria-label="Smiling senior couple embracing"></div>
  <div class="brand savings__brand"><span class="brand__mark"></span><span class="brand__name">Linden Medical</span></div>
  <h1 class="headline savings__headline"><span class="big">We Save</span><span class="sub">The patient, time and<br>money every month</span></h1>
  <svg class="bands" style="top:262px" height="80" viewBox="0 0 520 80">
    <polygon points="0,18 520,46 520,58 0,30" fill="var(--orange)"/>
    <polygon points="0,30 520,58 520,80 0,52" fill="var(--blue)"/>
  </svg>
  <ul class="features">
    <li class="feature">
      <svg class="feature__icon" viewBox="0 0 40 40"><rect x="6" y="16" width="28" height="20" fill="var(--green)"/><rect x="4" y="11" width="32" height="7" fill="var(--green)"/><rect x="18" y="11" width="4" height="25" fill="#fff"/><path d="M20 11c-4-8-12-6-8 0M20 11c4-8 12-6 8 0" stroke="var(--green)" stroke-width="3" fill="none"/></svg>
      <div><h2 class="feature__title">Free Meter <small>(when you qualify)</small></h2><p class="feature__text">Ask us about a no-cost glucose meter. We check your plan and ship the meter with your first supply order.</p></div>
    </li>
    <li class="feature">
      <svg class="feature__icon" viewBox="0 0 40 40"><circle cx="20" cy="20" r="17" fill="var(--green)"/><text x="20" y="27" text-anchor="middle" font-family="Open Sans,sans-serif" font-weight="700" font-size="20" fill="#fff">$</text></svg>
      <div><h2 class="feature__title">Save Money</h2><p class="feature__text">We research your insurance to get the most from your benefit, so you pay less for strips, lancets and medications.</p></div>
    </li>
    <li class="feature">
      <svg class="feature__icon" viewBox="0 0 40 40"><circle cx="20" cy="22" r="14" fill="none" stroke="var(--green)" stroke-width="4"/><path d="M20 14v9l6 4" stroke="var(--green)" stroke-width="3" fill="none"/><path d="M6 9l6-5M34 9l-6-5" stroke="var(--green)" stroke-width="4"/></svg>
      <div><h2 class="feature__title">Save Time</h2><p class="feature__text">No lines and no waiting. We contact your physician for authorization and handle every refill for you each month.</p></div>
    </li>
    <li class="feature">
      <svg class="feature__icon" viewBox="0 0 40 40"><rect x="2" y="10" width="22" height="18" fill="var(--green)"/><path d="M24 16h8l6 7v5H24z" fill="var(--green)"/><circle cx="10" cy="31" r="4" fill="var(--green)" stroke="#fff" stroke-width="2"/><circle cx="31" cy="31" r="4" fill="var(--green)" stroke="#fff" stroke-width="2"/></svg>
      <div><h2 class="feature__title">Free Delivery <small>right to your door</small></h2><p class="feature__text">Your testing supplies and oral medications arrive at your doorstep every month, with shipping always free of charge.</p></div>
    </li>
  </ul>
  <p class="savings__cta">Get started Today! Call our toll free number OR go to our website and fill our form.</p>
  <footer class="footer">
    <div class="footer__item footer__item--phone"><svg viewBox="0 0 16 16"><path d="M4 1l3 3-2 2c1 2 3 4 5 5l2-2 3 3-2 3C7 15 1 9 1 3z" fill="#fff"/></svg>800-555-0142</div>
    <div class="footer__item footer__item--web"><svg viewBox="0 0 16 16"><circle cx="8" cy="8" r="6.5" fill="none" stroke="#fff" stroke-width="1.5"/><path d="M1.5 8h13M8 1.5c-3 3-3 10 0 13M8 1.5c3 3 3 10 0 13" stroke="#fff" fill="none"/></svg>www.lindenmedical-rx.com</div>
    <div class="footer__item footer__item--mail"><svg viewBox="0 0 16 16"><rect x="1" y="3" width="14" height="10" fill="#fff"/><path d="M1 3l7 6 7-6" stroke="var(--blue)" fill="none"/></svg>care@lindenmedical-rx.com</div>
  </footer>
</section>

<section class="flyer flyer--pharmacy">
  <div class="photo pharmacy__photo" role="img" aria-label="Surprised woman peering over a bill"></div>
  <div class="brand pharmacy__brand"><span class="brand__mark"></span><span class="brand__name">Linden Medical</span></div>
  <div class="question">
    <p class="q1">Are the costs of your</p>
    <p class="q2">Diabetic testing supplies</p>
    <p class="q3">As high as your<br>blood sugar?</p>
  </div>
  <svg class="bands" style="top:290px" height="70" viewBox="0 0 520 70">
    <polygon points="0,40 520,14 520,24 0,50" fill="var(--orange)"/>
    <polygon points="0,50 520,24 520,42 0,68" fill="var(--blue)"/>
  </svg>
  <div class="badge">
    <svg viewBox="0 0 120 120" width="130" height="130"><polygon fill="var(--green)" points="60,2 69,16 85,8 88,25 105,24 100,41 116,48 104,60 116,72 100,79 105,96 88,95 85,112 69,104 60,118 51,104 35,112 32,95 15,96 20,79 4,72 16,60 4,48 20,41 15,24 32,25 35,8 51,16"/></svg>
    <div class="badge__text"><b>$20</b><span>GIFT CARD<br>is given with<br>your first order</span></div>
  </div>
  <h2 class="intro">We are a full service pharmacy that specializes in diabetic testing and medications.</h2>
  <div class="col col--left"><p>We are a full service pharmacy that specializes in diabetic testing. We research your insurance to determine how to save you the most money.</p></div>
  <div class="col col--right">
    <p>We then contact your physician to get the appropriate authorization.</p>
    <p>We ship your testing supplies and oral medications directly to your home for free! Testing supplies and oral medications.</p>
  </div>
  <div class="photo pharmacy__shelf" role="img" aria-label="Pharmacist reviewing stock at pharmacy shelves"></div>
  <div class="photo pharmacy__test" role="img" aria-label="Finger-prick blood glucose test with a meter"></div>
  <footer class="footer">
    <div class="footer__item footer__item--phone"><svg viewBox="0 0 16 16"><path d="M4 1l3 3-2 2c1 2 3 4 5 5l2-2 3 3-2 3C7 15 1 9 1 3z" fill="#fff"/></svg>800-555-0142</div>
    <div class="footer__item footer__item--web"><svg viewBox="0 0 16 16"><circle cx="8" cy="8" r="6.5" fill="none" stroke="#fff" stroke-width="1.5"/><path d="M1.5 8h13M8 1.5c-3 3-3 10 0 13M8 1.5c3 3 3 10 0 13" stroke="#fff" fill="none"/></svg>www.lindenmedical-rx.com</div>
    <div class="footer__item footer__item--mail"><svg viewBox="0 0 16 16"><rect x="1" y="3" width="14" height="10" fill="#fff"/><path d="M1 3l7 6 7-6" stroke="var(--blue)" fill="none"/></svg>care@lindenmedical-rx.com</div>
  </footer>
</section>

</body>
</html>
```